Bright and beautiful business card for a coach

I'm a personal and business coach based in Perth, Australia. I need a business card that whilst subtle and elegant, will stand out and appeal on a table full of cards.

My business name is Fern Mentoring and the business card must represent the warmth and brightness implied in the name, without being gimmicky. It must have a warmth and appeal and be easy to read.

I prefer clean, minimalist designs.

It must align with the feel of my website and socials: https://www.fernmentoring-example.com.au/
https://www.instagram.com/fernmentoringau/
https://www.facebook.com/fernmentoringau
Updates

Hi Designers Thank you so much for taking the time to submit designs. I wonder if I could have explained myself a little better. Most of the designs that have been submitted look rather formal and many have quite corporate looking embellishments on them (to my eye). I would like softer, warmer, more organic. I’m open to people playing about and being more abstract, using softer embellishments (e.g the line drawing flowers and grasses I’ve used in my socials) incorporating other colours from my palette or like the social icons in my email signature (in PDF), perhaps playing with size/oversize, playing with the bleed. Please don’t be constrained by what I’ve already done, it merely needs to compliment. I’m sorry if I’m not using the right words or have led you astray. I’m no designer, but I’ve done my website, socials, email signature etc all myself (my logo was a design contest) and I was really hoping for my business card to be something more creative than I could have made with a template. Reminder: No black cards/sides please. Thank you 😊

Target Market(s)

Individuals, most likely but not all female. Creative thinkers. Likely professionals.

Industry/Entity Type

Business & Personal Coach

Contact Information for Business Card

(Fern Mentoring Logo) Name: Greta Pellham; Title: Business & Personal Coach; Phone number: +61 (0)458 913307; Email: greta@fernmentoring-example.com.au; Website: https://fernmentoring-example.com.au; Social icons for Facebook, Instagram & LinkedIn: @fernmentoringAU. Optional strapline: "A thinking partner to help you cut through the noise"

Font styles to use
Sans Serif

Colors
00AB8E
00BBA5
67D7C9
C6EFE9
E9F9F6
59FF00
82FF00
B8FF75
E3FFCB
F4FFEA
FFC000
F8CF3A
FAE287
FDF2CF
FEFAEE

Requirements
Must have
• Must align with feel of my website and socials. Must have a pop of #FFC000 (possibly whole of one side, or at least a block). Bright or white background. Easy to read.
Nice to have
• Possibly incorporate the sunshine/grass picture I have used in website and socials - will upload.
Should not have
• Must not be black or dark. Not impersonal or corporate looking.

```html
<!DOCTYPE html>
<html lang="en">
<head>
<meta charset="utf-8">
<title>Fern Mentoring – Business Card</title>
<link href="https://fonts.googleapis.com/css2?family=Arimo:wght@400;700&display=swap" rel="stylesheet">
<style>
  :root{
    --bg:#eceae6;
    --card:#ffffff;
    --gold:#f0b62a;
    --gold-deep:#c9800f;
    --name:#c47a12;
    --ink:#555555;
    --rule:#8a8a8a;
    --photo-top:#6f9a34;
    --photo-bottom:#4f7a24;
    --portrait:#9a8a7c;
  }
  *{box-sizing:border-box;margin:0;padding:0}
  html,body{width:1200px;height:900px;overflow:hidden}
  body{background:var(--bg);font-family:"Arimo",Arial,sans-serif;position:relative}
  .card{
    position:absolute;left:270px;width:660px;height:400px;border-radius:22px;overflow:hidden;
    box-shadow:0 6px 18px rgba(0,0,0,.18);
  }
  .card--front{top:35px}
  .card--back{top:465px;background:var(--card)}

  .front-photo{
    position:absolute;inset:0;
    background:linear-gradient(180deg,var(--photo-top) 0%,var(--photo-bottom) 100%);
  }
  .brand{
    position:absolute;left:36px;top:34px;color:#fff;font-weight:400;font-size:30px;letter-spacing:.5px;
  }
  .tagline-band{
    position:absolute;left:0;right:0;top:300px;height:46px;
    background:linear-gradient(90deg,var(--gold-deep) 0%,#df9a20 50%,var(--gold) 100%);
    display:flex;align-items:center;justify-content:center;
  }
  .tagline{color:#fff;font-size:21px;letter-spacing:.2px}

  .portrait{
    position:absolute;left:62px;top:100px;width:196px;height:196px;border-radius:50%;
    border:3px solid var(--gold);padding:5px;background:#fff;
  }
  .portrait-fill{width:100%;height:100%;border-radius:50%;background:var(--portrait)}
  .divider{position:absolute;left:292px;top:100px;width:2px;height:200px;background:var(--rule)}
  .details{position:absolute;left:314px;top:98px;color:var(--ink)}
  .name{color:var(--name);font-size:31px;font-weight:400;letter-spacing:.5px;line-height:1}
  .role{font-size:20px;margin-top:6px;margin-bottom:14px}
  .contact{list-style:none}
  .contact li{display:flex;align-items:center;gap:9px;font-size:17px;line-height:1;margin-bottom:10px}
  .contact svg{width:16px;height:16px;flex:none}
  .socials{display:flex;align-items:center;gap:5px;margin-top:6px;font-size:19px}
  .social-square{width:18px;height:18px;border-radius:3px;background:var(--gold)}
  .socials .handle{margin-left:10px}
</style>
</head>
<body>
  <section class="card card--front" aria-label="Card front">
    <div class="front-photo" role="img" aria-label="Full-bleed photograph of sunlit grass"></div>
    <div class="brand">Fern Mentoring</div>
    <div class="tagline-band"><p class="tagline">A thinking partner to help you cut through the noise</p></div>
  </section>

  <section class="card card--back" aria-label="Card back">
    <div class="portrait"><div class="portrait-fill" role="img" aria-label="Portrait photo of Greta Pellham"></div></div>
    <div class="divider"></div>
    <div class="details">
      <h1 class="name">GRETA PELLHAM</h1>
      <p class="role">Business &amp; Personal Coach</p>
      <ul class="contact">
        <li>
          <svg viewBox="0 0 16 16" aria-hidden="true"><path fill="#e39a1f" d="M3.5 1.5l2.4 0 1 3.2-1.6 1.2a8 8 0 0 0 4.8 4.8l1.2-1.6 3.2 1v2.4c0 .8-.6 1.5-1.5 1.5A12.5 12.5 0 0 1 2 3c0-.9.7-1.5 1.5-1.5z"/></svg>
          +61 (0)458 913307
        </li>
        <li>
          <svg viewBox="0 0 16 16" aria-hidden="true"><rect x="1" y="3" width="14" height="10" rx="1" fill="#e39a1f"/><path d="M1.5 3.8 8 9l6.5-5.2" fill="none" stroke="#fff" stroke-width="1.3"/></svg>
          greta@fernmentoring-example.com.au
        </li>
        <li>
          <svg viewBox="0 0 16 16" aria-hidden="true"><circle cx="8" cy="8" r="7" fill="#e39a1f"/><path d="M1 8h14M8 1c-3 3-3 11 0 14M8 1c3 3 3 11 0 14" fill="none" stroke="#fff" stroke-width="1"/></svg>
          www.fernmentoring-example.com.au
        </li>
      </ul>
      <div class="socials">
        <span class="social-square" aria-hidden="true"></span>
        <span class="social-square" aria-hidden="true"></span>
        <span class="social-square" aria-hidden="true"></span>
        <span class="handle">@fernmentoringAU</span>
      </div>
    </div>
  </section>
</body>
</html>
```